Wellpath Ledgers New Website

Please review the attached Design Brief with additional details. Thank you!

The goal is to create a website that effectively communicates the benefits of WellPath Ledgers to eye care professionals. The website should streamline the process of understanding and utilizing WellPath Ledgers' services, emphasizing improved patient outcomes, increased referrals, and enhanced patient engagement.

Target Market(s)

Eyecare Professionals

Number of Pages Required

4 page

```html
<!DOCTYPE html>
<html lang="en">
<head>
<meta charset="utf-8">
<title>Wellpath Ledgers</title>
<link href="https://fonts.googleapis.com/css2?family=Open+Sans:wght@400;600;700;800&family=Lato:wght@400;700&display=swap" rel="stylesheet">
<style>
:root{
  --navy:#1b2a7c;
  --ink:#1f2530;
  --orange:#f7a331;
  --sky:#1d9bd8;
  --royal:#1f4f9e;
  --muted:#6b7280;
  --soft:#f2f2f2;
  --dark:#0e2342;
  --pale:#dfe7f1;
  --white:#fff;
}
*{box-sizing:border-box;margin:0;padding:0}
html,body{width:1200px;height:4967px;overflow:hidden}
body{position:relative;background:var(--white);font-family:"Lato",sans-serif;color:var(--ink)}
.abs{position:absolute}
.h{font-family:"Open Sans",sans-serif}
.btn{position:absolute;display:flex;align-items:center;justify-content:center;font-family:"Open Sans",sans-serif;font-weight:700;font-size:12px;color:#fff;background:var(--orange);border-radius:3px}
.label{position:absolute;font-family:"Open Sans",sans-serif;font-size:11px;font-weight:600;color:var(--sky);letter-spacing:.5px;display:flex;align-items:center;gap:10px}
.label i{display:block;width:46px;height:2px;background:var(--sky)}
.title{position:absolute;font-family:"Open Sans",sans-serif;font-weight:700;color:var(--navy);font-size:44px;line-height:1.3}
.body{font-size:12.5px;line-height:24px;color:#444}
.photo{position:absolute}

.topbar{left:0;top:0;width:1200px;height:140px;background:var(--soft)}
.brand{left:90px;top:10px}
.brand-name{display:flex;align-items:center;gap:8px;font-family:"Open Sans",sans-serif;font-weight:700;font-size:19px;color:var(--navy);line-height:1}
.brand-name b{width:14px;height:14px;background:var(--sky);display:block}
.brand-tag{font-size:9px;color:#333;margin:4px 0 0 22px}
.info{display:flex;gap:14px;align-items:center}
.info small{display:block;font-size:10px;color:#666;letter-spacing:.5px}
.info span{font-size:11px;color:#555}
.nav{left:85px;top:77px;width:1026px;height:66px;background:#fff;display:flex;align-items:center;padding-left:35px;gap:0;box-shadow:0 2px 6px rgba(0,0,0,.05);z-index:2}
.nav a{font-family:"Open Sans",sans-serif;font-weight:600;font-size:13px;color:#333;text-decoration:none;margin-right:58px}
.social{position:absolute;display:flex;gap:10px}
.social i{display:block;width:34px;height:34px;border-radius:3px}

.hero{left:0;top:106px;width:1200px;height:687px;background:linear-gradient(120deg,#3a4450,#1f2630 55%,#3b3f44)}
.hero-shade{left:0;top:106px;width:1200px;height:687px;background:rgba(20,25,35,.35)}
.arrow-box{position:absolute;width:62px;height:62px;background:#fff;border-radius:3px;display:flex;align-items:center;justify-content:center}

.service{position:absolute;top:1682px;width:320px;height:313px;border-radius:8px;overflow:hidden}
.service .bg{position:absolute;inset:0}
.service .ico{position:absolute;left:42px;top:45px;width:64px;height:64px;border-radius:8px;background:#fff;display:flex;align-items:center;justify-content:center}
.service h3{position:absolute;left:34px;top:146px;font-family:"Open Sans",sans-serif;font-size:22px;font-weight:700;color:#fff}
.service p{position:absolute;left:34px;top:214px;font-size:12px;color:#eee}
.service .more{position:absolute;left:34px;top:252px;font-family:"Open Sans",sans-serif;font-size:14px;font-weight:700;color:#fff}
.service .line{position:absolute;left:34px;right:34px;top:282px;height:2px;background:var(--sky)}

.why-item{position:absolute;width:220px}
.why-item h4{font-family:"Open Sans",sans-serif;font-size:19px;font-weight:600;color:var(--navy);margin-bottom:6px}
.why-item p{font-size:12px;line-height:20px;color:#555}
.why-ico{position:absolute;width:78px;height:78px;border-radius:50%;background:#fff;box-shadow:0 3px 14px rgba(0,0,0,.1);display:flex;align-items:center;justify-content:center}

.review{position:absolute;top:3260px;width:342px;height:206px;background:#fff;border-radius:10px;padding:24px 22px}
.review p{font-size:11.5px;line-height:24px;color:#666}
.review .who{position:absolute;left:22px;bottom:22px;display:flex;align-items:center;gap:14px;font-size:12px;color:#222}
.review .who i{width:40px;height:40px;border-radius:50%;background:linear-gradient(#d9c8b8,#8a6f5d);display:block}
.review .q{position:absolute;right:26px;bottom:34px;font-family:"Open Sans",sans-serif;font-size:44px;font-weight:800;color:#222;line-height:20px;height:22px}

.field{position:absolute;height:50px;border:1px solid #ddd;border-radius:3px;font-size:11px;color:#777;display:flex;align-items:center;padding-left:18px}

.foot-h{position:absolute;font-family:"Open Sans",sans-serif;font-size:17px;font-weight:700;color:#fff}
.foot-t{position:absolute;font-size:12.5px;color:#9aa7bb;line-height:22px}
.reach{position:absolute;top:4404px;width:344px;height:152px;display:flex;flex-direction:column;align-items:center;justify-content:center;gap:14px;font-family:"Open Sans",sans-serif;font-weight:700;font-size:15px;color:#222}
</style>
</head>
<body>

<div class="abs topbar"></div>
<div class="abs brand">
  <div class="brand-name"><b></b>Wellpath Ledgers</div>
  <div class="brand-tag">Empowering Healthcare</div>
</div>
<div class="abs info" style="left:430px;top:22px">
  <svg width="26" height="32" viewBox="0 0 26 32"><path d="M13 1C6.5 1 2 6 2 12c0 8 11 19 11 19s11-11 11-19C24 6 19.5 1 13 1z" fill="#1b2a4a"/><circle cx="13" cy="12" r="4" fill="#fff"/></svg>
  <div><small>LOCATION</small><span>48 Alder Rd, LA</span></div>
</div>
<div class="abs info" style="left:675px;top:22px">
  <svg width="38" height="38" viewBox="0 0 38 38"><circle cx="19" cy="20" r="15" fill="none" stroke="#1b2a4a" stroke-width="3"/><path d="M19 11v9l6 4" fill="none" stroke="#1b2a4a" stroke-width="3"/><circle cx="31" cy="7" r="4" fill="var(--sky)"/></svg>
  <div><small>OFFICE HOURS</small><span>9.00 to 7.00 [Sun: closed]</span></div>
</div>
<div class="btn" style="left:945px;top:23px;width:166px;height:45px;background:var(--navy);font-size:11px">REQUEST A QUOTE</div>

<nav class="abs nav">
  <a>Home</a><a>About Us</a><a>Services</a><a>Blog</a><a>Team</a><a>Contact Us</a>
  <div class="social" style="left:863px;top:16px">
    <i style="background:#3b5998"></i><i style="background:#e1306c"></i><i style="background:#1da1f2"></i>
  </div>
</nav>

<div class="photo hero" role="img" aria-label="Researcher working at a microscope in a laboratory"></div>
<div class="abs hero-shade"></div>
<div class="btn" style="left:511px;top:330px;width:160px;height:35px;font-weight:600;font-size:11px">WELCOME</div>
<h1 class="abs h" style="left:0;top:380px;width:1200px;text-align:center;color:#fff;font-size:58px;font-weight:700;line-height:72px">Insightful Data,<br>Better Outcomes</h1>
<div class="btn" style="left:507px;top:546px;width:168px;height:48px;background:transparent;border:2px solid #fff;font-size:11px">ABOUT COMPANY</div>
<div class="arrow-box" style="left:42px;top:488px"><svg width="22" height="14"><path d="M21 7H2M8 1 2 7l6 6" fill="none" stroke="#999" stroke-width="1.5"/></svg></div>
<div class="arrow-box" style="left:1094px;top:488px"><svg width="22" height="14"><path d="M1 7h19M14 1l6 6-6 6" fill="none" stroke="#999" stroke-width="1.5"/></svg></div>

<div class="abs" style="left:96px;top:916px;width:444px;height:444px;border-radius:50%;background:var(--navy)"></div>
<div class="photo" style="left:104px;top:916px;width:440px;height:440px;border-radius:50%;background:linear-gradient(150deg,#c9d6e2,#5d86b4 55%,#2f5f93)" role="img" aria-label="Nurse in blue scrubs holding a tablet"></div>
<div class="abs" style="left:434px;top:1260px;width:96px;height:96px;border-radius:50%;background:#fff;box-shadow:0 4px 14px rgba(0,0,0,.15)"></div>
<div class="label" style="left:612px;top:940px">ABOUT US <i></i></div>
<div class="title" style="left:610px;top:970px">Empowering Eye<br>Care Excellence</div>
<p class="abs body" style="left:612px;top:1103px;width:450px;color:#2a3a7c">Lorem ipsum dolor sit amet, consectetur adipiscing elit, sed do eiusmo empor incididunt ut abore et dolore magna aliqua. Ut enim ad minim iam, quis nostrud exercitation ullamco</p>
<p class="abs body" style="left:612px;top:1186px;width:450px;color:#2a3a7c">Lorem ipsum dolor sit amet, consectetur adipiscing elit, sed do eiusmo empor incididunt ut abore et dolore magna aliqua. Ut enim ad minim iam, quis nostrud exercitation ullamco</p>
<div class="btn" style="left:612px;top:1296px;width:168px;height:43px">Apply Now</div>

<div class="abs" style="left:0;top:1457px;width:1200px;height:826px;background:var(--soft)"></div>
<div class="label" style="left:90px;top:1542px">SERVICES <i></i></div>
<div class="title" style="left:88px;top:1574px">Services We Offer</div>
<div class="arrow-box" style="left:1000px;top:1559px;width:46px;height:62px"><svg width="10" height="16"><path d="M8 1 2 8l6 7" fill="none" stroke="#222" stroke-width="2"/></svg></div>
<div class="arrow-box" style="left:1052px;top:1559px;width:46px;height:62px"><svg width="10" height="16"><path d="m2 1 6 7-6 7" fill="none" stroke="#222" stroke-width="2"/></svg></div>

<div class="service" style="left:93px">
  <div class="bg" role="img" aria-label="Team reviewing health analytics at a table" style="background:linear-gradient(180deg,#8a7466,#3d3b45 70%,#2b2f3a)"></div>
  <div class="ico"><svg width="34" height="34"><circle cx="17" cy="17" r="11" fill="none" stroke="var(--orange)" stroke-width="2"/><circle cx="17" cy="17" r="4" fill="none" stroke="var(--orange)" stroke-width="2"/></svg></div>
  <h3>Health Analytics</h3><p>Lorem ipsum dolor sit amet, consectetur</p><div class="more">Read More</div><div class="line"></div>
</div>
<div class="service" style="left:440px">
  <div class="bg" role="img" aria-label="Smiling colleagues at a meeting" style="background:linear-gradient(180deg,#7e8a8f,#465058 70%,#2c3139)"></div>
  <div class="ico"><svg width="34" height="34"><path d="M8 28h18M12 24l10-14 4 3-10 14z" fill="none" stroke="var(--orange)" stroke-width="2"/></svg></div>
  <h3>Outcome Monitoring</h3><p>Lorem ipsum dolor sit amet, consectetur</p><div class="more">Read More</div><div class="line"></div>
</div>
<div class="service" style="left:787px">
  <div class="bg" role="img" aria-label="Professionals discussing data at a desk" style="background:linear-gradient(180deg,#9aa1a8,#4b5561 70%,#2d323b)"></div>
  <div class="ico"><svg width="34" height="34"><path d="M17 5l11 8-4 14H10L6 13z" fill="none" stroke="var(--orange)" stroke-width="2"/></svg></div>
  <h3>Data Management</h3><p>Lorem ipsum dolor sit amet, consectetur</p><div class="more">Read More</div><div class="line"></div>
</div>
<div class="btn" style="left:513px;top:2070px;width:166px;height:44px">Contact Us</div>

<div class="photo" style="left:95px;top:2180px;width:1014px;height:206px;border-radius:8px;background:linear-gradient(90deg,#1f4f9e,#2d62b4 60%,#1c4a96)" role="img" aria-label="Laboratory equipment under blue light"></div>
<div class="abs h" style="left:150px;top:2272px;font-size:22px;font-weight:700;color:#fff">Delivering Results with Solid Dependability</div>
<div class="btn" style="left:683px;top:2265px;width:164px;height:50px;background:transparent;border:2px solid #fff;font-weight:600">Get A Quote</div>
<div class="btn" style="left:855px;top:2265px;width:204px;height:50px;background:#fff;color:#222;font-weight:600;gap:8px">
  <svg width="16" height="16" viewBox="0 0 16 16"><path d="M3 1l3 3-2 2c1 2 3 4 5 5l2-2 3 3-2 3C6 14 2 10 1 3z" fill="#222"/></svg>+ 012 555 - 01920</div>

<div class="label" style="left:0;width:1200px;justify-content:center;top:2451px"><i></i>WHY US<i></i></div>
<div class="title" style="left:0;width:1200px;text-align:center;top:2470px">Why Choose Us</div>
<svg class="abs" style="left:350px;top:2600px" width="500" height="320"><path d="M45 50C8 100 8 210 45 270" fill="none" stroke="#333" stroke-width="1.4"/><path d="M455 50C492 100 492 210 455 270" fill="none" stroke="#333" stroke-width="1.4"/></svg>
<div class="photo" style="left:430px;top:2591px;width:328px;height:328px;border-radius:50%;background:linear-gradient(160deg,#6c83b3,#33467a 60%,#23325c)" role="img" aria-label="Smiling businessman with arms crossed"></div>

<div class="why-item" style="left:98px;top:2618px;text-align:right"><h4>Quality Assurance</h4><p>Lorem ipsum dolor sit amet,<br>consectetur adipiscing</p></div>
<div class="why-item" style="left:116px;top:2743px"><h4>Timely Assistance</h4><p>Lorem ipsum dolor sit amet,<br>consectetur adipiscing</p></div>
<div class="why-item" style="left:130px;top:2868px"><h4>Cost-Effective</h4><p>Lorem ipsum dolor sit amet,<br>consectetur adipiscing</p></div>
<div class="why-item" style="left:874px;top:2606px"><h4>Client-Centric</h4><p>Lorem ipsum dolor sit amet,<br>consectetur adipiscing</p></div>
<div class="why-item" style="left:897px;top:2743px"><h4>Proven Track Record</h4><p>Lorem ipsum dolor sit amet,<br>consectetur adipiscing</p></div>
<div class="why-item" style="left:874px;top:2868px"><h4>Quality Assurance</h4><p>Lorem ipsum dolor sit amet,<br>consectetur adipiscing</p></div>

<div class="why-ico" style="left:353px;top:2610px"><svg width="34" height="30"><circle cx="12" cy="9" r="5" fill="none" stroke="var(--orange)" stroke-width="2"/><circle cx="24" cy="11" r="4" fill="none" stroke="var(--orange)" stroke-width="2"/><path d="M3 27c1-7 17-7 18 0M20 22c3-3 10-2 11 4" fill="none" stroke="var(--orange)" stroke-width="2"/></svg></div>
<div class="why-ico" style="left:321px;top:2735px"><svg width="32" height="32"><circle cx="16" cy="16" r="13" fill="none" stroke="var(--orange)" stroke-width="2"/><path d="M10 22c3-4 9-4 12 0" fill="none" stroke="var(--orange)" stroke-width="2"/><circle cx="11" cy="13" r="1.8" fill="var(--orange)"/><circle cx="21" cy="13" r="1.8" fill="var(--orange)"/></svg></div>
<div class="why-ico" style="left:353px;top:2860px"><svg width="32" height="32"><circle cx="16" cy="16" r="12" fill="none" stroke="var(--orange)" stroke-width="2"/><path d="M16 9v14M12 13h6a3 3 0 0 1 0 6h-6" fill="none" stroke="var(--orange)" stroke-width="2"/></svg></div>
<div class="why-ico" style="left:762px;top:2610px"><svg width="34" height="34"><path d="M8 28h18M12 24l10-14 4 3-10 14z" fill="none" stroke="var(--orange)" stroke-width="2"/></svg></div>
<div class="why-ico" style="left:796px;top:2735px"><svg width="34" height="34"><path d="M17 4l4 9 9 1-7 6 2 10-8-5-8 5 2-10-7-6 9-1z" fill="none" stroke="var(--orange)" stroke-width="2"/></svg></div>
<div class="why-ico" style="left:762px;top:2860px"><svg width="34" height="34"><circle cx="17" cy="17" r="6" fill="none" stroke="var(--orange)" stroke-width="2"/><circle cx="17" cy="17" r="12" fill="none" stroke="var(--orange)" stroke-width="2" stroke-dasharray="4 3"/></svg></div>

<div class="abs" style="left:0;top:3057px;width:1200px;height:534px;background:var(--soft)"></div>
<div class="photo" style="left:0;top:3057px;width:338px;height:534px;background:linear-gradient(160deg,#3d6fbd,#1f4f9e)" role="img" aria-label="Doctor with stethoscope in blue tone"></div>
<div class="label" style="left:338px;width:862px;justify-content:center;top:3118px"><i></i>TESTIMONIALS<i></i></div>
<div class="title" style="left:338px;width:862px;text-align:center;top:3140px">Reviews from Clients</div>

<div class="review" style="left:139px"><p>Lorem ipsum dolor sit amet, consectetur adipiscing elit, sed do eiusmod tempor incididunt ut labore et dolore magna aliqua. Ut enim ad minim veniam, quis nostrud exercitation</p><div class="who"><i></i>Mara Ellison</div><div class="q">"</div></div>
<div class="review" style="left:503px;border-bottom:3px solid var(--orange)"><p>Lorem ipsum dolor sit amet, consectetur adipiscing elit, sed do eiusmod tempor incididunt ut labore et dolore magna aliqua. Ut enim ad minim veniam, quis nostrud exercitation</p><div class="who"><i></i>Mara Ellison</div><div class="q">"</div></div>
<div class="review" style="left:872px"><p>Lorem ipsum dolor sit amet, consectetur adipiscing elit, sed do eiusmod tempor incididunt ut labore et dolore magna aliqua. Ut enim ad minim veniam, quis nostrud exercitation</p><div class="who"><i></i>Mara Ellison</div><div class="q">"</div></div>

<svg class="abs" style="left:628px;top:3505px" width="110" height="20"><circle cx="10" cy="10" r="7" fill="none" stroke="var(--sky)" stroke-width="1.5"/><circle cx="10" cy="10" r="3" fill="var(--sky)"/><circle cx="40" cy="10" r="3" fill="#999"/><circle cx="70" cy="10" r="3" fill="#999"/><circle cx="100" cy="10" r="3" fill="#999"/></svg>

<div class="label" style="left:0;width:1200px;justify-content:center;top:3712px"><i></i>CONTACT US<i></i></div>
<div class="title" style="left:0;width:1200px;text-align:center;top:3733px">Get in touch with us</div>
<div class="abs" style="left:93px;top:3846px;width:1014px;height:413px;background:#fff;box-shadow:0 4px 20px rgba(0,0,0,.08)"></div>
<div class="photo" style="left:93px;top:3846px;width:418px;height:413px;background:linear-gradient(150deg,#c8cdd2,#6b7480 50%,#3b3f47)" role="img" aria-label="Two colleagues smiling over a tablet"></div>
<div class="abs h" style="left:285px;top:4180px;width:224px;height:58px;background:#fff;display:flex;align-items:center;justify-content:center;gap:10px;font-weight:600;font-size:16px;color:#222">
  <svg width="18" height="18" viewBox="0 0 16 16"><path d="M3 1l3 3-2 2c1 2 3 4 5 5l2-2 3 3-2 3C6 14 2 10 1 3z" fill="#222"/></svg>1800-555-0142</div>
<div class="abs h" style="left:554px;top:3892px;font-size:22px;font-weight:700;color:#222">Get Free Consultation</div>
<p class="abs" style="left:554px;top:3928px;width:490px;font-size:13px;line-height:24px;color:#777">Get a free consultation from our experts, Our customer support team help you 24/7. Don't hesitate.</p>
<div class="field" style="left:554px;top:4010px;width:501px">Your Name</div>
<div class="field" style="left:554px;top:4080px;width:235px">Your Email</div>
<div class="field" style="left:818px;top:4080px;width:237px">Message</div>
<div class="btn" style="left:554px;top:4147px;width:501px;height:52px;font-size:11px;gap:6px">GET IN TOUCH <svg width="16" height="8"><path d="M0 4h14M11 1l3 3-3 3" fill="none" stroke="#fff" stroke-width="1.4"/></svg></div>

<div class="abs" style="left:0;top:4404px;width:1200px;height:505px;background:var(--dark)"></div>
<svg class="abs" style="left:110px;top:4372px" width="990" height="34"><path d="M6 2 980 30 0 32z" fill="#e6ecf3"/></svg>
<div class="abs" style="left:85px;top:4404px;width:1030px;height:152px;background:#fff"></div>
<div class="abs" style="left:428px;top:4430px;width:1px;height:100px;background:#e3e3e3"></div>
<div class="abs" style="left:772px;top:4430px;width:1px;height:100px;background:#e3e3e3"></div>
<div class="reach" style="left:85px"><svg width="44" height="40"><path d="M22 4c-7 0-11 5-11 10 0 7 11 16 11 16s11-9 11-16c0-5-4-10-11-10z" fill="none" stroke="var(--orange)" stroke-width="2"/><circle cx="22" cy="14" r="4" fill="none" stroke="var(--orange)" stroke-width="2"/><path d="M4 38l6-10h24l6 10z" fill="none" stroke="var(--orange)" stroke-width="1.6"/></svg>Come to Our Location</div>
<div class="reach" style="left:428px"><svg width="44" height="40"><rect x="4" y="14" width="36" height="24" fill="none" stroke="var(--orange)" stroke-width="2"/><path d="M4 14l18 14 18-14M12 14V4h20v10" fill="none" stroke="var(--orange)" stroke-width="2"/></svg>Send Us an Email</div>
<div class="reach" style="left:772px"><svg width="44" height="40" viewBox="0 0 16 16"><path d="M3 1l3 3-2 2c1 2 3 4 5 5l2-2 3 3-2 3C6 14 2 10 1 3z" fill="none" stroke="var(--orange)" stroke-width=".8"/></svg>Give Us a Call</div>

<div class="abs brand-name" style="left:85px;top:4618px;font-size:30px;color:var(--sky);font-weight:600"><b style="width:22px;height:22px"></b>Wellpath Ledgers</div>
<p class="foot-t" style="left:85px;top:4684px;width:310px">Lorem ipsum dolor sit amet, consectetur adipiscing elit, sed do eiusmod tempor ut labore et dolore magna aliqua. Ut enim ad minim veniam, quis nostrud exercitation ullamco laboris</p>

<div class="foot-h" style="left:438px;top:4616px">Visit Our Place</div>
<p class="foot-t" style="left:438px;top:4684px">17 Linden Road<br>Suite 4, 10021, USA</p>
<div class="abs" style="left:438px;top:4743px;font-size:11px;font-weight:700;color:#fff;text-decoration:underline">FIND US ON MAP</div>
<div class="abs" style="left:438px;top:4796px;width:305px;height:42px;border:1px solid #51627c;display:flex;font-size:10px;color:#9aa7bb">
  <span style="flex:1;padding:14px 12px">Enter Your Email...</span>
  <span style="width:100px;border-left:1px solid #51627c;padding:13px 0;text-align:center;color:var(--sky);font-weight:700;font-size:12px">SUBSCRIBE</span>
</div>

<div class="foot-h" style="left:789px;top:4616px">Useful Links</div>
<p class="foot-t" style="left:789px;top:4684px;line-height:33.5px">About Us<br>Practice areas<br>Why Choose Us<br>How it works<br>News &amp; Updates</p>
<p class="foot-t" style="left:959px;top:4684px;line-height:33.5px">Testimonials<br>FAQs<br>Cookies<br>Contact Us<br>Privacy Policy</p>

<div class="abs" style="left:0;top:4909px;width:1200px;height:58px;background:var(--pale)"></div>
<div class="abs h" style="left:85px;top:4930px;font-size:12px;font-weight:600;color:#222">Wellpath Ledgers</div>
<div class="social" style="left:1035px;top:4933px;gap:14px">
  <i style="width:9px;height:9px;background:#222;border-radius:50%"></i><i style="width:9px;height:9px;background:#222;border-radius:50%"></i><i style="width:9px;height:9px;background:#222;border-radius:50%"></i><i style="width:9px;height:9px;background:#222;border-radius:50%"></i>
</div>
<div class="abs" style="left:1138px;top:4899px;width:50px;height:50px;background:var(--orange);border-radius:3px;display:flex;align-items:center;justify-content:center"><svg width="18" height="12"><path d="M2 10l7-7 7 7" fill="none" stroke="#fff" stroke-width="3"/></svg></div>

</body>
</html>
```